WP website design Pellow - Brantz (Contest)

We need a wordpress design that will incorporate a professional color scheme with company logo in a clean layout. The design needs to consider that this will be developed on a responsive theme. Colors are red and black of the logo and and an accent color. Client wants a 'modern' look.

Industry/Entity Type

It Company

Font styles to use
Serif
Sans Serif

Colors

Designer to choose colors to be used in the design.

Requirements
Must have
• Must Have:
- Navigation: 1) Home; 2) Auctions; 3) Real Estate Listings 4) Assets For Sale 5) Services 6) About Us 7) Contact Us

Site will have slideshow - image is attached. Colors will be those in the logo, red and black with maybe an accent color. A site the client mentions liking is Mubrelbids.com for the use of color and layout.

Widgets: Featured Auctions, 2) Email signup form; 3) Testimonials blog widget; 5) Featured Video; Footer will have affiliation logo and contact info.

Home page content:
We are a family owned and operated business with over 25 years of real estate experience in Elk Ridge and surrounding areas in the Prairie Valley region. We know that purchasing a home is one of the most important decisions a person can make, and we strive to make it a successful and enjoyable experience for you!
Enjoy our website and please call if you have any questions or would like to make an appointment to view property!
Also, take a moment to look at our Auction Calendar for upcoming auction dates. Auctions are a great opportunity for great deals and rare finds, not to mention A LOT OF FUN!!

Widgets: 1) Featured Properties; 2) Call to action for Sellers 3) Testimonials blog/widget
Nice to have
• use of dropdown menus

```html
<!DOCTYPE html>
<html lang="en">
<head>
<meta charset="utf-8">
<title>Pellow - Brantz Auction &amp; Real Estate</title>
<link href="https://fonts.googleapis.com/css2?family=Open+Sans:wght@400;600;700&display=swap" rel="stylesheet">
<style>
:root{
  --red:#c8102e;
  --dark:#2b2b2b;
  --darker:#1e1e1e;
  --teal:#3bb49a;
  --text:#555;
  --muted:#888;
  --line:#e2e2e2;
  --footer:#ececec;
  --white:#fff;
}
*{box-sizing:border-box;margin:0;padding:0}
html,body{width:696px;height:1200px;overflow:hidden}
body{font-family:"Open Sans",Arial,sans-serif;color:var(--text);background:var(--white);position:relative}
.wrap{position:absolute;left:76px;width:546px}

/* header */
.site-header{position:absolute;top:0;left:0;width:696px;height:92px}
.brand{position:absolute;left:76px;top:24px}
.brand-name{font-size:24px;font-weight:700;color:var(--red);line-height:1}
.brand-tag{font-size:9px;color:var(--dark);margin-top:5px;letter-spacing:.5px}
.follow{position:absolute;right:74px;top:18px;text-align:left}
.follow-label{font-size:9px;color:var(--dark);margin-bottom:6px}
.social{display:flex;gap:5px}
.social span{width:15px;height:15px;border-radius:50%;background:var(--dark)}

/* nav */
.main-nav{position:absolute;top:92px;left:0;width:696px;height:22px;background:var(--dark)}
.main-nav ul{list-style:none;display:flex;position:absolute;left:76px;height:22px}
.main-nav li{font-size:9px;color:var(--white);padding:0 11px;line-height:22px;position:relative}
.main-nav li.active{background:var(--red)}
.dropdown{position:absolute;top:22px;left:0;width:96px;background:var(--red);padding:4px 0;z-index:3}
.dropdown div{font-size:8px;line-height:17px;padding-left:10px}
.dropdown div::before{content:"› ";}

/* hero */
.hero{position:absolute;top:114px;left:0;width:696px;height:266px;
  background:linear-gradient(180deg,#9fb38a 0%,#7d9560 40%,#b79b64 75%,#9a7d4c 100%)}

/* welcome */
.welcome{top:398px;text-align:center}
.welcome h1{font-size:21px;font-weight:600;color:var(--dark)}
.welcome h1 em{font-style:normal;color:var(--red)}
.welcome p{font-size:8.5px;line-height:14px;margin:18px auto 0;width:520px;color:var(--muted)}
.btn-red{display:inline-block;background:var(--red);color:var(--white);font-size:9px;padding:6px 14px;margin-top:18px}

/* headings */
.section-title{font-size:15px;font-weight:600;color:var(--dark)}
.section-title em{font-style:normal;color:var(--red)}

/* auctions */
.auctions{top:612px;width:364px}
.auction-card{border:1px solid var(--line);height:210px;margin-top:10px;padding:12px;position:relative}
.auction-card:first-of-type{margin-top:14px}
.thumb{position:absolute;left:12px;top:12px;width:120px;height:82px;background:linear-gradient(180deg,#9cc0e0,#c9b79a 70%,#7e9b5a)}
.card-links{position:absolute;left:12px;top:102px;width:120px;display:flex;flex-wrap:wrap;gap:4px 14px;font-size:7px;color:var(--dark)}
.card-links span::before{content:"";display:inline-block;width:6px;height:5px;background:var(--dark);margin-right:3px}
.btn-teal{position:absolute;left:12px;top:150px;width:120px;height:42px;background:var(--teal);color:var(--white);text-align:center;font-size:7px;padding-top:8px}
.btn-teal b{display:block;font-size:10px;font-weight:600;margin-top:2px}
.card-body{position:absolute;left:146px;top:12px;right:12px}
.card-body h3{font-size:11px;font-weight:600;color:var(--teal)}
.card-body p{font-size:7.5px;line-height:11px;color:var(--muted);margin-top:6px}
.card-body h4{font-size:9px;font-weight:600;color:var(--dark);margin-top:9px}
.dates{font-size:7.5px;line-height:12px;margin-top:4px;color:var(--muted)}
.dates b{color:var(--red);font-weight:600}
.card-body hr{border:0;border-top:1px solid var(--line);margin-top:8px}

/* sidebar */
.sidebar{position:absolute;left:460px;width:162px;top:612px}
.alert-box{background:var(--dark);padding:10px;margin-top:14px;height:80px}
.alert-box label{display:block;font-size:8px;color:var(--white)}
.alert-box .input{background:var(--white);height:16px;margin-top:6px;font-size:7px;color:#aaa;padding:3px 5px}
.alert-box .submit{float:right;background:var(--red);color:var(--white);font-size:7px;padding:3px 8px;margin-top:8px}
.sidebar .section-title.spaced{margin-top:20px}
.testimonial{border:1px solid var(--line);margin-top:12px;height:92px;padding:10px;position:relative}
.avatar{position:absolute;left:10px;top:12px;width:30px;height:30px;border-radius:50%;background:#d9b9a4}
.testimonial p{margin-left:42px;font-size:7.5px;line-height:11px;color:var(--muted)}
.testimonial .by{margin-left:42px;font-size:7px;color:var(--red);margin-top:4px}
.video{margin-top:12px;height:140px;background:linear-gradient(180deg,#3a3a3a,#151515);position:relative}
.video svg{position:absolute;left:61px;top:50px}

/* footer */
.site-footer{position:absolute;top:1095px;left:0;width:696px;height:83px;background:var(--footer)}
.badges{position:absolute;left:76px;top:14px;width:170px;display:flex;flex-wrap:wrap;gap:6px}
.badges span{width:36px;height:24px;background:#555}
.badges span.wide{width:72px;background:#777}
.f-follow{position:absolute;left:296px;top:12px}
.f-title{font-size:11px;font-weight:600;color:var(--red)}
.f-follow .social{margin-top:8px}
.contact{position:absolute;left:490px;top:12px;font-size:7.5px;line-height:11px;color:var(--text)}
.contact .f-title{margin-bottom:4px}
.copyright{position:absolute;top:1178px;left:0;width:696px;height:22px;background:var(--darker);color:#bbb;font-size:7.5px;text-align:center;line-height:22px}
</style>
</head>
<body>

<header class="site-header">
  <div class="brand">
    <div class="brand-name">Pellow - Brantz</div>
    <div class="brand-tag">Auction &amp; Real Estate</div>
  </div>
  <div class="follow">
    <div class="follow-label">Follow Us</div>
    <div class="social"><span></span><span></span><span></span><span></span><span></span></div>
  </div>
</header>

<nav class="main-nav">
  <ul>
    <li>Home</li>
    <li class="active">Auctions
      <div class="dropdown"><div>Upcoming Auctions</div><div>Past Auctions</div></div>
    </li>
    <li>Real Estate Listings</li>
    <li>Assets For Sale</li>
    <li>Services</li>
    <li>About Us</li>
    <li>Contact Us</li>
  </ul>
</nav>

<div class="hero" role="img" aria-label="Slideshow photo: auction sign in a sunny field with trees behind"></div>

<section class="wrap welcome">
  <h1>Welcome to Our <em>Site!</em></h1>
  <p>We are a family run business with more than two decades of real estate and auction experience in Elk Ridge and the towns across the Prairie Valley region. We know that buying a home is one of the biggest choices a person can make, and we work hard to make it a smooth and happy experience for you! Enjoy our website, and please give us a call with any questions or to book a time to view a property.</p>
  <span class="btn-red">Read More</span>
</section>

<section class="wrap auctions">
  <h2 class="section-title">Featured <em>Auctions</em></h2>

  <article class="auction-card">
    <div class="thumb" role="img" aria-label="Photo of a brick family home"></div>
    <div class="card-links"><span>Details</span><span>Photos</span><span>Videos</span></div>
    <div class="btn-teal">Click here for<b>Online Bidding &gt;&gt;</b></div>
    <div class="card-body">
      <h3>Finibus Bonorum et Malorum</h3>
      <p>Duis aute irure dolor in reprehenderit in voluptate velit esse cillum dolore eu fugiat nulla pariatur.</p>
      <h4>Online Bidding Only</h4>
      <div class="dates"><b>Begins:</b> Tuesday, May 30, 2017 at 11:00 AM CST<br><b>Ends:</b> Wednesday, May 31, 2017 at 11:00 AM CST</div>
      <hr>
      <h4>Live Off-Site Auction</h4>
      <div class="dates"><b>Begins:</b> Tuesday, May 30, 2017 at 11:00 AM CST<br><b>Ends:</b> Wednesday, May 31, 2017 at 11:00 AM CST</div>
    </div>
  </article>

  <article class="auction-card">
    <div class="thumb" role="img" aria-label="Photo of a two-storey house with a lawn"></div>
    <div class="card-links"><span>Details</span><span>Photos</span><span>Videos</span></div>
    <div class="btn-teal">Click here for<b>Online Bidding &gt;&gt;</b></div>
    <div class="card-body">
      <h3>Finibus Bonorum et Malorum</h3>
      <p>Duis aute irure dolor in reprehenderit in voluptate velit esse cillum dolore eu fugiat nulla pariatur.</p>
      <h4>Online Bidding Only</h4>
      <div class="dates"><b>Begins:</b> Tuesday, May 30, 2017 at 11:00 AM CST<br><b>Ends:</b> Wednesday, May 31, 2017 at 11:00 AM CST</div>
      <hr>
      <h4>Live Off-Site Auction</h4>
      <div class="dates"><b>Begins:</b> Tuesday, May 30, 2017 at 11:00 AM CST<br><b>Ends:</b> Wednesday, May 31, 2017 at 11:00 AM CST</div>
    </div>
  </article>
</section>

<aside class="sidebar">
  <h2 class="section-title"><em>Auction</em> Alerts</h2>
  <div class="alert-box">
    <label>Email sign-up form</label>
    <div class="input">Enter your Email</div>
    <span class="submit">SUBMIT</span>
  </div>

  <h2 class="section-title spaced">Testimonials</h2>
  <div class="testimonial">
    <div class="avatar" role="img" aria-label="Client portrait"></div>
    <p>“Duis aute irure dolor in reprehenderit in voluptate velit esse cillum dolore eu fugiat nulla.”</p>
    <div class="by">by Dana Reyes</div>
  </div>

  <h2 class="section-title spaced">Featured <em>Video</em></h2>
  <div class="video" role="img" aria-label="Featured auction video">
    <svg width="40" height="40" viewBox="0 0 40 40"><circle cx="20" cy="20" r="18" fill="none" stroke="#fff" stroke-width="2"/><path d="M16 12 L29 20 L16 28 Z" fill="#fff"/></svg>
  </div>
</aside>

<footer class="site-footer">
  <div class="badges"><span></span><span></span><span></span><span></span><span class="wide"></span></div>
  <div class="f-follow">
    <div class="f-title">Follow Us</div>
    <div class="social"><span></span><span></span><span></span><span></span><span></span></div>
  </div>
  <div class="contact">
    <div class="f-title">Contact Info</div>
    Pellow - Brantz Co.<br>
    210 Prairie Lane, Elk Ridge PV 40120<br>
    Tel: (555) 014 2280<br>
    Email: hello@pellowbrantz.test
  </div>
</footer>
<div class="copyright">Copyright © 2024 Pellow - Brantz . All right reserved.</div>

</body>
</html>
```